TorbCutters Website & website development in Wordpress

Simple website for a 5 pages with some 15 products for sale.
We will sell T shirts and other Viking mens grooming products.

*****Lady barbers****
Also the company that gets awarded this job needs to be able to give me a quote to build the site in wordpress, just a design will not work.

Target Market(s)

The adventurous person likes to travels and get a good haircut

Coding

Coded - Design and coding required

Number of Pages Required

5+ page

Font styles to use
Sans Serif

Colors
3176b5
33a6d7

Requirements
Must have
• Must have a product order page for T-Shirts
Must have a travel adventure page with up to 5 recommended adventures
Must have a link to our instagram @torbcuttersformen page that would allow a client to book a haircut
Should show female stylists cutting mens hair- So far the only pictures in the designs submitted are male barbers
Nice to have
• We have this set up in GoDaddy would like to use wordpress. Thanks!

```html
<!DOCTYPE html>
<html lang="en">
<head>
<meta charset="utf-8">
<title>Torb Men's Grooming – Homepage Colour Variants</title>
<link href="https://fonts.googleapis.com/css2?family=Montserrat:wght@500;600;700;800&family=Lato:wght@400;700&family=Lora:wght@400&display=swap" rel="stylesheet">
<style>
:root{
  --stage:#7b7b7b;
  --ink:#161616;
  --dark:#000;
  --white:#fff;
  --tint:#eaf1fa;
  --muted:#444;
  --star:#e2b100;
  --red:#e1242b;
  --blue:#33a6d7;
  --head:'Montserrat',sans-serif;
  --body:'Lato',sans-serif;
  --serif:'Lora',serif;
}
*{margin:0;padding:0;box-sizing:border-box}
html,body{width:827px;height:1200px;overflow:hidden}
body{background:var(--stage);position:relative;font-family:var(--body);color:var(--ink)}
.page{position:absolute;top:22px;width:386px;height:1155px;background:var(--white);overflow:hidden}
.page--red{left:19px;--accent:var(--red)}
.page--blue{left:422px;--accent:var(--blue)}
.abs{position:absolute}

/* hero */
.hero{position:absolute;left:0;top:0;width:386px;height:191px;
  background:linear-gradient(180deg,#4a4038 0%,#5c4a3c 35%,#3a2a1e 70%,#2a1c12 100%)}
.hero-photo{position:absolute;inset:0;
  background:radial-gradient(ellipse 80px 60px at 160px 70px,#7a3a22 0%,transparent 100%),
             radial-gradient(ellipse 40px 30px at 300px 90px,#e9e4dc 0%,transparent 100%),
             linear-gradient(180deg,rgba(0,0,0,.1),rgba(0,0,0,.35))}
.brand{position:absolute;left:38px;top:20px;font-family:var(--head);font-weight:800;font-size:9px;color:var(--white);display:flex;align-items:center;gap:3px}
.brand-dot{width:7px;height:7px;border-radius:50%;background:var(--accent)}
.nav{position:absolute;top:22px;left:0;font-family:var(--head);font-weight:600;font-size:5px;color:var(--white)}
.nav span{position:absolute;white-space:nowrap}
.cart-count{position:absolute;width:4px;height:4px;border-radius:50%;background:var(--accent);font-size:3px;line-height:4px;text-align:center}
.hero-title{position:absolute;left:37px;top:77px;font-family:var(--head);font-weight:800;font-size:16.5px;line-height:18.6px;color:var(--white);letter-spacing:.2px}
.btn{display:inline-block;font-family:var(--head);font-weight:700;color:var(--white);text-align:center;border-radius:10px;background:var(--accent)}
.hero-buy{position:absolute;left:36px;top:143px;width:54px;height:15px;font-size:5px;line-height:15px}
.hero-more{position:absolute;left:98px;top:143px;font-family:var(--head);font-weight:700;font-size:5px;line-height:15px;color:var(--white)}

/* perks */
.perks{position:absolute;left:0;top:191px;width:386px;height:42px;background:var(--dark);color:var(--white)}
.perk{position:absolute;top:13px;display:flex;gap:5px}
.perk svg{width:7px;height:7px;margin-top:1px}
.perk p{font-size:4.4px;line-height:7.8px}
.perk b{font-weight:700}

/* welcome */
.welcome{position:absolute;left:0;top:233px;width:386px;height:215px;background:var(--white)}
.welcome-shape{position:absolute;left:0;top:0}
.welcome-photo{position:absolute;left:36px;top:44px;width:103px;height:145px;
  background:linear-gradient(180deg,#6fb4ec 0%,#a9cbe6 35%,#4c6f92 60%,#3d4c5a 100%)}
.eyebrow{position:absolute;left:206px;top:57px;font-family:var(--body);font-size:6px;color:var(--ink);display:flex;align-items:center;gap:3px}
.welcome h2{position:absolute;left:207px;top:69px;font-family:var(--body);font-weight:400;font-size:11px;color:var(--ink);white-space:nowrap}
.lead{position:absolute;left:208px;top:86px;width:150px;font-family:var(--serif);font-size:5.2px;line-height:7.8px;color:var(--ink)}
.copy{position:absolute;left:207px;top:107px;width:140px;font-size:4.6px;line-height:7.7px;color:var(--muted)}
.text-link{position:absolute;left:208px;top:156px;font-size:4.8px;color:var(--accent)}

/* products */
.products{position:absolute;left:0;top:448px;width:386px;height:386px;background:var(--tint)}
.section-title{position:absolute;left:0;width:386px;text-align:center;font-family:var(--head);font-weight:700;font-size:11.5px;color:var(--ink)}
.section-sub{position:absolute;left:85px;width:216px;text-align:center;font-family:var(--serif);font-size:5px;line-height:7.8px;color:var(--ink)}
.card{position:absolute;width:80px;height:141px;background:var(--white);box-shadow:0 0 2px rgba(0,0,0,.12)}
.card-img{position:absolute;left:6px;top:6px;width:68px;height:68px}
.sale{position:absolute;left:5px;top:3px;width:17px;height:17px;border-radius:50%;background:var(--accent);color:var(--white);font-family:var(--head);font-weight:700;font-size:4.2px;line-height:17px;text-align:center}
.card-name{position:absolute;top:82px;width:80px;text-align:center;font-family:var(--head);font-weight:600;font-size:5px}
.stars{position:absolute;top:92px;width:80px;text-align:center;font-size:5px;color:var(--star);letter-spacing:.3px}
.price{position:absolute;top:101px;width:80px;text-align:center;font-family:var(--head);font-weight:700;font-size:5px;color:var(--accent)}
.card-btn{position:absolute;left:17px;top:115px;width:47px;height:14px;border:.6px solid #333;border-radius:1px;font-family:var(--head);font-weight:600;font-size:4.3px;line-height:13px;text-align:center}

/* appointment */
.appointment{position:absolute;left:0;top:834px;width:386px;height:67px;background:var(--white)}
.appointment h2{position:absolute;left:46px;top:13px;font-family:var(--head);font-weight:700;font-size:11.5px}
.appointment p{position:absolute;left:46px;top:33px;width:190px;font-family:var(--serif);font-size:5px;line-height:7.8px}
.book-btn{position:absolute;left:275px;top:24px;width:64px;height:16px;font-size:5px;line-height:16px;border-radius:8px}

/* footer */
.footer{position:absolute;left:0;top:901px;width:386px;height:254px;background:var(--dark);color:var(--white)}
.footer-title{position:absolute;left:0;top:16px;width:386px;text-align:center;font-family:var(--head);font-weight:700;font-size:11.5px}
.email-field{position:absolute;left:76px;top:41px;width:174px;height:18px;border-radius:9px;background:var(--white);color:#444;font-size:5px;line-height:18px;padding-left:10px}
.subscribe{position:absolute;left:255px;top:41px;width:58px;height:18px;font-size:5px;line-height:18px;border-radius:9px}
.rule{position:absolute;left:36px;width:314px;height:.5px;background:#333}
.partner{position:absolute;top:82px;width:28px;height:30px;border-radius:50%;background:#3a3a3a}
.col-head{position:absolute;top:140px;font-family:var(--head);font-weight:700;font-size:5.4px}
.col{position:absolute;top:153px;font-size:4.6px;line-height:10px;color:#ddd}
.col.tight{line-height:7.7px;width:84px}
.social{position:absolute;top:188px;width:12px;height:12px;border-radius:50%;background:var(--white)}
.copyright{position:absolute;left:0;top:231px;width:386px;text-align:center;font-size:4.6px;color:#ddd}
</style>
</head>
<body>

<!-- ============ RED VARIANT ============ -->
<div class="page page--red">
  <header class="hero">
    <div class="hero-photo" role="img" aria-label="Photo of a leather grooming bag with shaving brushes, razor, cologne bottles and shaving foam bowl on a wooden table"></div>
    <div class="brand"><span class="brand-dot"></span>TorbCutters</div>
    <nav class="nav">
      <span style="left:122px">HOME</span><span style="left:150px">ABOUT</span><span style="left:182px">BLOG</span>
      <span style="left:209px">SERVICE</span><span style="left:243px">SHOP</span><span style="left:270px">CONTACT</span>
      <span style="left:308px">
        <svg width="6" height="5" viewBox="0 0 6 5"><path d="M0 .5h1l1 3h3l.6-2.2H1.5" fill="none" stroke="#fff" stroke-width=".6"/><circle cx="2.3" cy="4.5" r=".4" fill="#fff"/><circle cx="4.5" cy="4.5" r=".4" fill="#fff"/></svg>
      </span>
      <span class="cart-count" style="left:312px;top:-2px">0</span>
      <span style="left:319px;font-weight:500;font-size:4.4px">$0.00</span>
    </nav>
    <h1 class="hero-title">TORB MEN'S<br>GROOMING<br>PRODUCTS</h1>
    <span class="btn hero-buy">BUY NOW</span>
    <span class="hero-more">MORE INFO</span>
  </header>

  <section class="perks">
    <div class="perk" style="left:36px"><svg viewBox="0 0 8 8"><rect x="1" y="3" width="6" height="4.5" fill="none" stroke="var(--accent)" stroke-width=".7"/><path d="M.6 2.2h6.8v1H.6zM4 2.2v5.3" fill="none" stroke="var(--accent)" stroke-width=".7"/></svg><p>Hessle-Free Returns<br><b>30 Day Easy Return</b></p></div>
    <div class="perk" style="left:118px"><svg viewBox="0 0 8 8"><path d="M.5 2h4.5v4H.5zM5 3.5h1.7L7.5 5v1H5z" fill="none" stroke="var(--accent)" stroke-width=".7"/><circle cx="2" cy="6.6" r=".8" fill="var(--accent)"/><circle cx="6" cy="6.6" r=".8" fill="var(--accent)"/></svg><p>For Orders Above $250<br><b>Free Delivery</b></p></div>
    <div class="perk" style="left:203px"><svg viewBox="0 0 8 8"><path d="M.5 4a3.5 3 0 0 1 7 0zM4 4v3a.8.8 0 0 1-1.5 0" fill="none" stroke="var(--accent)" stroke-width=".7"/></svg><p>Shop With Confidence<br><b>10 Year Warranty</b></p></div>
    <div class="perk" style="left:289px"><svg viewBox="0 0 8 8"><path d="M1 5V4a3 3 0 0 1 6 0v1" fill="none" stroke="var(--accent)" stroke-width=".7"/><rect x=".7" y="4.3" width="1.6" height="2.6" fill="var(--accent)"/><rect x="5.7" y="4.3" width="1.6" height="2.6" fill="var(--accent)"/></svg><p>Ready To Help<br><b>24/7 Help Center</b></p></div>
  </section>

  <section class="welcome">
    <svg class="welcome-shape" width="386" height="215" viewBox="0 0 386 215">
      <path d="M52 23h40q5 0 7 6l6 15H62z" fill="var(--accent)"/>
      <path d="M180 23h29l-62 155h-8l55-146q3-9 10-9z" fill="var(--accent)" transform="translate(-4 0)"/>
    </svg>
    <div class="welcome-photo" role="img" aria-label="Photo of a traveller with arms outstretched on a rocky summit facing snowy mountains"></div>
    <p class="eyebrow">SED UT PERSPICIATIS
      <svg width="20" height="16" viewBox="0 0 20 16"><path d="M1 2l17 12M18 1L2 13" stroke="var(--accent)" stroke-width=".8"/><circle cx="17" cy="3" r="1.8" fill="none" stroke="var(--accent)" stroke-width=".7"/><circle cx="17.5" cy="13" r="1.8" fill="none" stroke="var(--accent)" stroke-width=".7"/></svg>
    </p>
    <h2>Welcome To Torb men's</h2>
    <p class="lead">But I must explain to you how all this mistaken idea of denouncing pleasure and praising pain was born and I will</p>
    <p class="copy">Sed ut perspiciatis unde omnis iste natus error sit voluptatem accusantium doloremque laudantium, totam rem aperiam, eaque ipsa quae ab illo inventore veritatis et quasi architecto beatae vitae dicta sunt explicabo. Nemo enim ipsam voluptatem quia voluptas sit aspernatur aut odit aut fugit</p>
    <a class="text-link">Take Travel Adventure</a>
  </section>

  <section class="products">
    <h2 class="section-title" style="top:12px">Our Product</h2>
    <p class="section-sub" style="top:31px">Sed ut perspiciatis unde omnis iste natus error sit voluptatem accusantium doloremque laudantium, totam rem aperiam, eaque ipsa quae</p>

    <div class="card" style="left:19px;top:68px"><div class="card-img" role="img" aria-label="Aluminium comb product photo" style="background:radial-gradient(ellipse 34px 8px,#9a9a9a 0%,#fff 100%)"></div><p class="card-name">Aluminium Comb</p><p class="stars">★★★★☆</p><p class="price">$20.00</p><p class="card-btn">ADD TO CART</p></div>
    <div class="card" style="left:108px;top:68px"><div class="card-img" role="img" aria-label="Grooming trimmer product photo" style="background:radial-gradient(ellipse 8px 30px,#222 0%,#fff 100%)"></div><p class="card-name">Grooming Trimmer</p><p class="stars">★★★★☆</p><p class="price">$20.00</p><p class="card-btn">ADD TO CART</p></div>
    <div class="card" style="left:198px;top:68px"><div class="card-img" role="img" aria-label="Black comb product photo" style="background:radial-gradient(ellipse 34px 6px,#1a1a1a 0%,#fff 100%)"></div><span class="sale">Sale!</span><p class="card-name">Torb Comb</p><p class="stars">★★★★☆</p><p class="price">$20.00</p><p class="card-btn">ADD TO CART</p></div>
    <div class="card" style="left:287px;top:68px"><div class="card-img" role="img" aria-label="Electric trimmer product photo" style="background:radial-gradient(ellipse 9px 26px,#333 0%,#fff 100%)"></div><span class="sale">Sale!</span><p class="card-name">Torb Trimmer</p><p class="stars">★★★★☆</p><p class="price">$20.00</p><p class="card-btn">ADD TO CART</p></div>

    <div class="card" style="left:19px;top:220px"><div class="card-img" role="img" aria-label="Black branded t-shirt product photo" style="background:radial-gradient(ellipse 28px 28px,#111 0%,#fff 100%)"></div><p class="card-name">Brave T Shirt</p><p class="stars">★★★★☆</p><p class="price">$20.00</p><p class="card-btn">ADD TO CART</p></div>
    <div class="card" style="left:108px;top:220px"><div class="card-img" role="img" aria-label="Red shaver spray bottle product photo" style="background:radial-gradient(ellipse 22px 30px,#e8343a 0%,#f3f3f3 100%)"></div><p class="card-name">Shaver spray</p><p class="stars">★★★★☆</p><p class="price">$20.00</p><p class="card-btn">ADD TO CART</p></div>
    <div class="card" style="left:198px;top:220px"><div class="card-img" role="img" aria-label="Yellow t-shirt product photo" style="background:radial-gradient(ellipse 26px 30px,#f2b81b 0%,#fff 100%)"></div><span class="sale">Sale!</span><p class="card-name">Torb T Shirt</p><p class="stars">★★★★☆</p><p class="price">$20.00</p><p class="card-btn">ADD TO CART</p></div>
    <div class="card" style="left:287px;top:220px"><div class="card-img" role="img" aria-label="Amber beard oil dropper bottle product photo" style="background:radial-gradient(ellipse 9px 26px,#5a2d12 0%,#fff 100%)"></div><p class="card-name">Beard Oil</p><p class="stars">★★★★☆</p><p class="price">$20.00</p><p class="card-btn">ADD TO CART</p></div>
  </section>

  <section class="appointment">
    <h2>Book An Appointment</h2>
    <p>Sed ut perspiciatis unde omnis iste natus error sit voluptatem accusantium doloremque laudantium,</p>
    <span class="btn book-btn">BOOK NOW</span>
  </section>

  <footer class="footer">
    <h2 class="footer-title">Stay Informed With Our Latest News</h2>
    <div class="email-field">Enter Your Email</div>
    <span class="btn subscribe">SUBSCRIBE</span>
    <div class="rule" style="top:78px"></div>
    <span class="partner" style="left:45px"></span><span class="partner" style="left:96px"></span><span class="partner" style="left:151px"></span>
    <span class="partner" style="left:204px"></span><span class="partner" style="left:257px"></span><span class="partner" style="left:310px"></span>
    <div class="rule" style="top:133px"></div>
    <h3 class="col-head" style="left:32px">ABOUT OUR COMPANY</h3>
    <p class="col tight" style="left:32px;top:154px">Sed ut perspiciatis unde omnis iste natus error sit voluptatem accusantium doloremque laudantium, totam rem aperiam, eaque ipsa quae ab illo inventore veritatis et quasi</p>
    <h3 class="col-head" style="left:126px">CONTACT INFO</h3>
    <p class="col" style="left:126px">⌖ Sed ut perspiciatis unde omnis<br>✆ 155-010-2222<br>▤ 021 555 014<br>✉ hello@torbgrooming.com</p>
    <h3 class="col-head" style="left:213px">CUSTOMER SERVICE</h3>
    <p class="col" style="left:213px">Ask in forum<br>Help Desk<br>FAQ<br>Terms &amp; Conditions</p>
    <h3 class="col-head" style="left:288px">OPENING TIME</h3>
    <p class="col tight" style="left:288px;top:152px;width:90px">Mon – Fri: 08:30 am – 09:30 pm<br>Sat – Sun: 09:00 am – 10:00 pm</p>
    <h3 class="col-head" style="left:288px;top:174px">FOLLOW US</h3>
    <span class="social" style="left:287px"></span><span class="social" style="left:301px"></span><span class="social" style="left:316px"></span><span class="social" style="left:330px"></span>
    <div class="rule" style="top:215px"></div>
    <p class="copyright">© 2021 Torb Men's Grooming All Rights Reserved</p>
  </footer>
</div>

<!-- ============ BLUE VARIANT ============ -->
<div class="page page--blue">
  <header class="hero">
    <div class="hero-photo" role="img" aria-label="Photo of a leather grooming bag with shaving brushes, razor, cologne bottles and shaving foam bowl on a wooden table"></div>
    <div class="brand"><span class="brand-dot"></span>TorbCutters</div>
    <nav class="nav">
      <span style="left:122px">HOME</span><span style="left:150px">ABOUT</span><span style="left:182px">BLOG</span>
      <span style="left:209px">SERVICE</span><span style="left:243px">SHOP</span><span style="left:270px">CONTACT</span>
      <span style="left:308px">
        <svg width="6" height="5" viewBox="0 0 6 5"><path d="M0 .5h1l1 3h3l.6-2.2H1.5" fill="none" stroke="#fff" stroke-width=".6"/><circle cx="2.3" cy="4.5" r=".4" fill="#fff"/><circle cx="4.5" cy="4.5" r=".4" fill="#fff"/></svg>
      </span>
      <span class="cart-count" style="left:312px;top:-2px">0</span>
      <span style="left:319px;font-weight:500;font-size:4.4px">$0.00</span>
    </nav>
    <h1 class="hero-title">TORB MEN'S<br>GROOMING<br>PRODUCTS</h1>
    <span class="btn hero-buy">BUY NOW</span>
    <span class="hero-more">MORE INFO</span>
  </header>

  <section class="perks">
    <div class="perk" style="left:36px"><svg viewBox="0 0 8 8"><rect x="1" y="3" width="6" height="4.5" fill="none" stroke="var(--accent)" stroke-width=".7"/><path d="M.6 2.2h6.8v1H.6zM4 2.2v5.3" fill="none" stroke="var(--accent)" stroke-width=".7"/></svg><p>Hessle-Free Returns<br><b>30 Day Easy Return</b></p></div>
    <div class="perk" style="left:118px"><svg viewBox="0 0 8 8"><path d="M.5 2h4.5v4H.5zM5 3.5h1.7L7.5 5v1H5z" fill="none" stroke="var(--accent)" stroke-width=".7"/><circle cx="2" cy="6.6" r=".8" fill="var(--accent)"/><circle cx="6" cy="6.6" r=".8" fill="var(--accent)"/></svg><p>For Orders Above $250<br><b>Free Delivery</b></p></div>
    <div class="perk" style="left:203px"><svg viewBox="0 0 8 8"><path d="M.5 4a3.5 3 0 0 1 7 0zM4 4v3a.8.8 0 0 1-1.5 0" fill="none" stroke="var(--accent)" stroke-width=".7"/></svg><p>Shop With Confidence<br><b>10 Year Warranty</b></p></div>
    <div class="perk" style="left:289px"><svg viewBox="0 0 8 8"><path d="M1 5V4a3 3 0 0 1 6 0v1" fill="none" stroke="var(--accent)" stroke-width=".7"/><rect x=".7" y="4.3" width="1.6" height="2.6" fill="var(--accent)"/><rect x="5.7" y="4.3" width="1.6" height="2.6" fill="var(--accent)"/></svg><p>Ready To Help<br><b>24/7 Help Center</b></p></div>
  </section>

  <section class="welcome">
    <svg class="welcome-shape" width="386" height="215" viewBox="0 0 386 215">
      <path d="M52 23h40q5 0 7 6l6 15H62z" fill="var(--accent)"/>
      <path d="M180 23h29l-62 155h-8l55-146q3-9 10-9z" fill="var(--accent)" transform="translate(-4 0)"/>
    </svg>
    <div class="welcome-photo" role="img" aria-label="Photo of a traveller with arms outstretched on a rocky summit facing snowy mountains"></div>
    <p class="eyebrow">SED UT PERSPICIATIS
      <svg width="20" height="16" viewBox="0 0 20 16"><path d="M1 2l17 12M18 1L2 13" stroke="var(--accent)" stroke-width=".8"/><circle cx="17" cy="3" r="1.8" fill="none" stroke="var(--accent)" stroke-width=".7"/><circle cx="17.5" cy="13" r="1.8" fill="none" stroke="var(--accent)" stroke-width=".7"/></svg>
    </p>
    <h2>Welcome To Torb men's</h2>
    <p class="lead">But I must explain to you how all this mistaken idea of denouncing pleasure and praising pain was born and I will</p>
    <p class="copy">Sed ut perspiciatis unde omnis iste natus error sit voluptatem accusantium doloremque laudantium, totam rem aperiam, eaque ipsa quae ab illo inventore veritatis et quasi architecto beatae vitae dicta sunt explicabo. Nemo enim ipsam voluptatem quia voluptas sit aspernatur aut odit aut fugit</p>
    <a class="text-link">Take Travel Adventure</a>
  </section>

  <section class="products">
    <h2 class="section-title" style="top:12px">Our Product</h2>
    <p class="section-sub" style="top:31px">Sed ut perspiciatis unde omnis iste natus error sit voluptatem accusantium doloremque laudantium, totam rem aperiam, eaque ipsa quae</p>

    <div class="card" style="left:19px;top:68px"><div class="card-img" role="img" aria-label="Aluminium comb product photo" style="background:radial-gradient(ellipse 34px 8px,#9a9a9a 0%,#fff 100%)"></div><p class="card-name">Aluminium Comb</p><p class="stars">★★★★☆</p><p class="price">$20.00</p><p class="card-btn">ADD TO CART</p></div>
    <div class="card" style="left:108px;top:68px"><div class="card-img" role="img" aria-label="Grooming trimmer product photo" style="background:radial-gradient(ellipse 8px 30px,#222 0%,#fff 100%)"></div><p class="card-name">Grooming Trimmer</p><p class="stars">★★★★☆</p><p class="price">$20.00</p><p class="card-btn">ADD TO CART</p></div>
    <div class="card" style="left:198px;top:68px"><div class="card-img" role="img" aria-label="Black comb product photo" style="background:radial-gradient(ellipse 34px 6px,#1a1a1a 0%,#fff 100%)"></div><span class="sale">Sale!</span><p class="card-name">Torb Comb</p><p class="stars">★★★★☆</p><p class="price">$20.00</p><p class="card-btn">ADD TO CART</p></div>
    <div class="card" style="left:287px;top:68px"><div class="card-img" role="img" aria-label="Electric trimmer product photo" style="background:radial-gradient(ellipse 9px 26px,#333 0%,#fff 100%)"></div><span class="sale">Sale!</span><p class="card-name">Torb Trimmer</p><p class="stars">★★★★☆</p><p class="price">$20.00</p><p class="card-btn">ADD TO CART</p></div>

    <div class="card" style="left:19px;top:220px"><div class="card-img" role="img" aria-label="Black branded t-shirt product photo" style="background:radial-gradient(ellipse 28px 28px,#111 0%,#fff 100%)"></div><p class="card-name">Brave T Shirt</p><p class="stars">★★★★☆</p><p class="price">$20.00</p><p class="card-btn">ADD TO CART</p></div>
    <div class="card" style="left:108px;top:220px"><div class="card-img" role="img" aria-label="Red shaver spray bottle product photo" style="background:radial-gradient(ellipse 22px 30px,#e8343a 0%,#f3f3f3 100%)"></div><p class="card-name">Shaver spray</p><p class="stars">★★★★☆</p><p class="price">$20.00</p><p class="card-btn">ADD TO CART</p></div>
    <div class="card" style="left:198px;top:220px"><div class="card-img" role="img" aria-label="Yellow t-shirt product photo" style="background:radial-gradient(ellipse 26px 30px,#f2b81b 0%,#fff 100%)"></div><span class="sale">Sale!</span><p class="card-name">Torb T Shirt</p><p class="stars">★★★★☆</p><p class="price">$20.00</p><p class="card-btn">ADD TO CART</p></div>
    <div class="card" style="left:287px;top:220px"><div class="card-img" role="img" aria-label="Amber beard oil dropper bottle product photo" style="background:radial-gradient(ellipse 9px 26px,#5a2d12 0%,#fff 100%)"></div><p class="card-name">Beard Oil</p><p class="stars">★★★★☆</p><p class="price">$20.00</p><p class="card-btn">ADD TO CART</p></div>
  </section>

  <section class="appointment">
    <h2>Book An Appointment</h2>
    <p>Sed ut perspiciatis unde omnis iste natus error sit voluptatem accusantium doloremque laudantium,</p>
    <span class="btn book-btn">BOOK NOW</span>
  </section>

  <footer class="footer">
    <h2 class="footer-title">Stay Informed With Our Latest News</h2>
    <div class="email-field">Enter Your Email</div>
    <span class="btn subscribe">SUBSCRIBE</span>
    <div class="rule" style="top:78px"></div>
    <span class="partner" style="left:45px"></span><span class="partner" style="left:96px"></span><span class="partner" style="left:151px"></span>
    <span class="partner" style="left:204px"></span><span class="partner" style="left:257px"></span><span class="partner" style="left:310px"></span>
    <div class="rule" style="top:133px"></div>
    <h3 class="col-head" style="left:32px">ABOUT OUR COMPANY</h3>
    <p class="col tight" style="left:32px;top:154px">Sed ut perspiciatis unde omnis iste natus error sit voluptatem accusantium doloremque laudantium, totam rem aperiam, eaque ipsa quae ab illo inventore veritatis et quasi</p>
    <h3 class="col-head" style="left:126px">CONTACT INFO</h3>
    <p class="col" style="left:126px">⌖ Sed ut perspiciatis unde omnis<br>✆ 155-010-2222<br>▤ 021 555 014<br>✉ hello@torbgrooming.com</p>
    <h3 class="col-head" style="left:213px">CUSTOMER SERVICE</h3>
    <p class="col" style="left:213px">Ask in forum<br>Help Desk<br>FAQ<br>Terms &amp; Conditions</p>
    <h3 class="col-head" style="left:288px">OPENING TIME</h3>
    <p class="col tight" style="left:288px;top:152px;width:90px">Mon – Fri: 08:30 am – 09:30 pm<br>Sat – Sun: 09:00 am – 10:00 pm</p>
    <h3 class="col-head" style="left:288px;top:174px">FOLLOW US</h3>
    <span class="social" style="left:287px"></span><span class="social" style="left:301px"></span><span class="social" style="left:316px"></span><span class="social" style="left:330px"></span>
    <div class="rule" style="top:215px"></div>
    <p class="copyright">© 2021 Torb Men's Grooming All Rights Reserved</p>
  </footer>
</div>

</body>
</html>
```